Business Card design for law firm = Brightvale Australia

We are seeking a new design for our business cards.
We are keeping our logo, which is attached.
We need space for
Name
Title
Address is , which is
Level 7
214 Marlowe Street
Sydney NSW 2047
Phone :
Mobile :
Fax :
Email :
DX :
website www.brightvale-example.com.au

Industry/Entity Type

Law Firm / Banking and Finance

Contact Information for Business Card

We are seeking a new design for our business cards. We are keeping our logo. We need space for Name Title Address is Level 7 214 Marlowe Street Sydney NSW 2047 Phone Mobile Fax Email DX website www.brightvale-example.com.au

Colors
0054AA
0677BA
7BADD7
CADEEF
E8F1F8

Requirements
Must have
• see our website for general feel www.brightvale-example.com.au

```html
<!DOCTYPE html>
<html lang="en">
<head>
<meta charset="utf-8">
<title>Brightvale Australia business card</title>
<link rel="stylesheet" href="https://fonts.googleapis.com/css2?family=Sorts+Mill+Goudy&display=swap">
<style>
  :root {
    --brand-blue: #0054AA;
    --mid-blue: #0677BA;
    --front-blue: #1E5CAA;
    --soft-blue: #7BADD7;
    --pale-blue: #CADEEF;
    --ink: #2b2b2b;
    --paper: #ffffff;
    --faint: #efefef;
    --stage: #3a3a3c;
  }
  * { box-sizing: border-box; margin: 0; padding: 0; }
  html, body { width: 1200px; height: 900px; overflow: hidden; }
  body {
    background: var(--stage);
    display: flex; flex-direction: column; align-items: center; justify-content: center;
    gap: 56px;
    font-family: "Sorts Mill Goudy", Georgia, serif;
  }
  .card {
    position: relative; width: 600px; height: 343px;
    border-radius: 22px; overflow: hidden;
    box-shadow: 0 10px 28px rgba(0,0,0,.35);
  }
  .card--front { background: var(--front-blue); color: var(--paper); }
  .card--back { background: linear-gradient(160deg, var(--paper) 0%, #f2f2f2 55%, var(--paper) 100%); color: var(--ink); }

  .brand { position: absolute; display: flex; align-items: center; gap: 14px; }
  .brand__dot { width: 26px; height: 26px; border-radius: 50%; flex: none; }
  .brand__name { font-size: 44px; line-height: 1; }

  .card--front .brand { left: 50%; top: 50%; transform: translate(-50%, -50%); }
  .card--front .brand__dot { background: var(--pale-blue); }
  .card--front .brand__name { color: var(--paper); }

  .back-accent { position: absolute; right: 60px; top: -60px; width: 200px; height: 200px; border-radius: 50%; background: var(--faint); }

  .person { position: absolute; left: 36px; top: 30px; }
  .person__name { color: var(--mid-blue); font-size: 24px; line-height: 1.1; }
  .person__title { font-size: 17px; }

  .contacts { position: absolute; left: 44px; top: 98px; list-style: none; font-size: 16px; line-height: 21px; }
  .contacts li { display: flex; align-items: center; gap: 10px; }
  .contacts svg { width: 14px; height: 14px; flex: none; }

  .divider { position: absolute; left: 0; top: 208px; width: 350px; height: 1px; background: var(--soft-blue); }

  .card--back .brand { left: 58px; top: 246px; }
  .card--back .brand__dot { background: var(--mid-blue); }
  .card--back .brand__name { color: var(--brand-blue); }

  .address { position: absolute; left: 372px; top: 176px; font-size: 16px; line-height: 21px; font-style: normal; display: flex; gap: 10px; }
  .address svg { width: 14px; height: 18px; margin-top: 3px; flex: none; }
  .address__dx { color: var(--brand-blue); font-size: 18px; }
</style>
</head>
<body>

<section class="card card--front" aria-label="Card front">
  <div class="brand">
    <span class="brand__dot"></span>
    <span class="brand__name">Brightvale</span>
  </div>
</section>

<section class="card card--back" aria-label="Card back">
  <div class="back-accent"></div>

  <div class="person">
    <div class="person__name">Sam Ridley</div>
    <div class="person__title">Managing Director</div>
  </div>

  <ul class="contacts">
    <li><svg viewBox="0 0 14 14"><path d="M1 4c0-2 3-3 6-3s6 1 6 3v1h-3V4H4v1H1z M3 6h8l1 7H2z" fill="var(--brand-blue)"/></svg>02 9470 3185</li>
    <li><svg viewBox="0 0 14 14"><rect x="3.5" y="0.5" width="7" height="13" rx="1.5" fill="none" stroke="var(--brand-blue)"/><circle cx="7" cy="11.3" r=".8" fill="var(--brand-blue)"/></svg>04 1286 5530</li>
    <li><svg viewBox="0 0 14 14"><rect x="3" y="1" width="8" height="5" fill="none" stroke="var(--brand-blue)"/><rect x="1" y="6" width="12" height="6" rx="1" fill="none" stroke="var(--brand-blue)"/></svg>02 9470 3199</li>
    <li><svg viewBox="0 0 14 14"><rect x="1" y="3" width="12" height="9" rx="1" fill="var(--brand-blue)"/><path d="M1.5 3.5 7 8l5.5-4.5" fill="none" stroke="#fff"/></svg>enquiries@brightvale-example.com.au</li>
    <li><svg viewBox="0 0 14 14"><circle cx="7" cy="7" r="6" fill="none" stroke="var(--brand-blue)"/><path d="M1 7h12M7 1c-3 3-3 9 0 12M7 1c3 3 3 9 0 12" fill="none" stroke="var(--brand-blue)"/></svg>www.brightvale-example.com.au</li>
  </ul>

  <div class="divider"></div>

  <div class="brand">
    <span class="brand__dot"></span>
    <span class="brand__name">Brightvale</span>
  </div>

  <address class="address">
    <svg viewBox="0 0 14 18"><path d="M7 1a6 6 0 0 0-6 6c0 4.5 6 10 6 10s6-5.5 6-10a6 6 0 0 0-6-6z" fill="var(--brand-blue)"/><circle cx="7" cy="7" r="2.2" fill="#fff"/></svg>
    <div>
      Level 7, 214 Marlowe Street<br>
      Sydney NSW 2047<br>
      <span class="address__dx">DX 318 Sydney</span>
    </div>
  </address>
</section>

</body>
</html>
```